Verodex business card

Business card for sustainable investment company called "Verodex". Verodex is an exchange platform selling carbon credits between buyers and sellers. Carbon Credits are an environmental commodity for reducing global carbon emissions.

the card should obviously have our logo and the theme should be sustainability/environment mixed with a trading platform.

Contact Information for Business Card

Logo, Name, Title, Phone, Email

Colors
0054AA
0677BA
7BADD7
CADEEF
E8F1F8
0094D4
00A9DD
6FCCEA
C7EBF8
E9F6FB
00AB8E
00BBA5
67D7C9
C6EFE9
E9F9F6
59FF00
82FF00
B8FF75
E3FFCB
F4FFEA

```html
<!DOCTYPE html>
<html lang="en">
<head>
<meta charset="utf-8">
<title>Verodex business card</title>
<link href="https://fonts.googleapis.com/css2?family=Montserrat:wght@400;500;700&display=swap" rel="stylesheet">
<style>
  :root{
    --stage:#1c1d20;
    --card-dark:#0a0b0d;
    --card-light:#27282b;
    --accent:#4aa6de;
    --accent-deep:#2f8fd0;
    --ink:#ffffff;
    --rule:#3f9fd8;
  }
  *{margin:0;padding:0;box-sizing:border-box}
  html,body{width:1200px;height:900px;overflow:hidden}
  body{
    background:var(--stage);
    font-family:"Montserrat",Arial,sans-serif;
    color:var(--ink);
    display:flex;flex-direction:column;align-items:center;justify-content:center;gap:40px;
  }
  .card{
    position:relative;width:640px;height:366px;
    background:linear-gradient(120deg,var(--card-dark) 0%,var(--card-dark) 40%,var(--card-light) 100%);
    box-shadow:0 10px 30px rgba(0,0,0,.55);
  }
  .brand{display:flex;align-items:center;gap:16px}
  .brand-dot{width:40px;height:40px;border-radius:50%;background:var(--accent)}
  .brand-name{font-weight:700;font-size:44px;letter-spacing:1px;color:var(--ink)}
  .card--front .brand{position:absolute;left:50%;top:50%;transform:translate(-50%,-50%)}
  .card--back .brand{position:absolute;right:34px;top:52px}
  .card--back .brand-dot{width:32px;height:32px}
  .card--back .brand-name{font-size:36px}
  .holder{position:absolute;left:30px;top:120px;padding-left:26px}
  .holder::before{content:"";position:absolute;left:0;top:2px;width:12px;height:34px;background:var(--accent-deep)}
  .holder-name{font-weight:700;font-size:22px;color:var(--accent);letter-spacing:.5px;line-height:1}
  .holder-title{font-size:14px;letter-spacing:1px;margin-top:6px}
  .rule{position:absolute;left:30px;right:34px;top:182px;height:1px;background:var(--rule)}
  .contacts{position:absolute;left:30px;top:202px;list-style:none;font-size:15px}
  .contacts li{display:flex;align-items:center;gap:12px;height:28px}
  .contacts svg{width:16px;height:16px;fill:none;stroke:var(--accent);stroke-width:1.6}
  .address{position:absolute;right:34px;bottom:34px;text-align:right;font-size:15px;line-height:1.45}
</style>
</head>
<body>
  <section class="card card--front">
    <div class="brand"><span class="brand-dot"></span><span class="brand-name">VERODEX</span></div>
  </section>

  <section class="card card--back">
    <div class="brand"><span class="brand-dot"></span><span class="brand-name">VERODEX</span></div>
    <div class="holder">
      <p class="holder-name">DALEN RUSK</p>
      <p class="holder-title">MANAGER</p>
    </div>
    <div class="rule"></div>
    <ul class="contacts">
      <li><svg viewBox="0 0 16 16"><path d="M4 2l2.5 3-1.5 1.5c.8 1.8 2.2 3.2 4 4L10.5 9l3 2.5-1.5 2C7 13 3 9 2.5 4z"/></svg>555-308-4172</li>
      <li><svg viewBox="0 0 16 16"><rect x="2" y="4" width="12" height="9"/><path d="M2 4l6 5 6-5"/></svg>info@verodexmail.com</li>
      <li><svg viewBox="0 0 16 16"><circle cx="8" cy="8" r="6"/><path d="M2 8h12M8 2c-3 3-3 9 0 12M8 2c3 3 3 9 0 12"/></svg>www.verodexsite.com</li>
    </ul>
    <p class="address">2417 Harbor Crest Rd. Linden Park<br>Ave Fairview, MN 05521</p>
  </section>
</body>
</html>
```